Destination PDF Template (Editable)

Objective: Create a visually stunning and compelling PDF brochure that showcases The Vorelka Crest Lodge as the ultimate luxury hunting destination in Kyrgyzstan, specializing in Marco Polo and Ibex hunts. The PDF should evoke a sense of exclusivity, adventure, and the breathtaking beauty of the Tian Shan mountains, ultimately driving bookings.
Target Audience: High-net-worth individuals, discerning hunters seeking exceptional experiences, adventure travelers, and those interested in unique and luxurious wilderness experiences.
Overall Tone & Style: Sophisticated, elegant, and aspirational. Think high-end travel magazines combined with a touch of rugged adventure. Avoid anything that feels generic or overly commercial. The design should reflect the unparalleled nature of the lodge and the hunts offered. (I'm attaching a reference PDF that i like), as well as another instructions file. Drive link for photos: https://files.pondery-share.net/box/folders/7KqLm2xVbR4tWz9hN3cJpE6yF0aDs8uG?mode=open
Another Link: https://files.pondery-share.net/box/u/0/folders/9ZtRe4wQmN2bVx7kLp5sHc8jYd3fGa1oU

```html
<!DOCTYPE html>
<html lang="en">
<head>
<meta charset="utf-8">
<title>The Vorelka Crest Lodge — Brochure</title>
<link rel="stylesheet" href="https://fonts.googleapis.com/css2?family=Libre+Baskerville:ital,wght@0,400;0,700;1,400&family=Montserrat:wght@400;500;600&display=swap">
<style>
  :root{
    --canvas:#8c8c8c;
    --paper:#ffffff;
    --ink:#1f1f1f;
    --crimson:#a8232f;
    --rose:#c9505d;
    --blush:#f1d3d7;
    --charcoal:#232323;
    --gutter:#f4f1ee;
  }
  *{box-sizing:border-box;margin:0;padding:0}
  html,body{width:1200px;height:4968px;overflow:hidden}
  body{background:var(--canvas);font-family:'Montserrat',sans-serif;color:var(--ink)}
  .page{position:absolute;left:383px;width:434px;height:614px;background:var(--paper);overflow:hidden}
  .photo{position:absolute}
  .serif{font-family:'Libre Baskerville',serif}
  .brand{position:absolute;font-family:'Montserrat',sans-serif;font-weight:600;display:flex;align-items:center;gap:5px}
  .brand .dot{width:9px;height:9px;border-radius:50%;background:currentColor}
  .small{font-size:7.2px;line-height:1.32;text-align:justify}

  /* cover */
  .cover-photo{inset:0;background:
    radial-gradient(ellipse 60% 30% at 30% 72%,rgba(196,160,118,.85),rgba(196,160,118,0) 70%),
    radial-gradient(ellipse 40% 45% at 62% 50%,rgba(70,72,64,.7),rgba(70,72,64,0) 70%),
    radial-gradient(ellipse 70% 25% at 70% 35%,rgba(235,232,228,.9),rgba(235,232,228,0) 70%),
    linear-gradient(180deg,#e2e3e6 0%,#c9c6c2 22%,#a08e7b 45%,#7a6350 68%,#4e3d30 100%)}
  .cover-title{position:absolute;left:40px;right:40px;top:88px;height:90px;background:rgba(255,255,255,.5);border-radius:6px;text-align:center;padding-top:10px}
  .cover-title p{font-family:'Libre Baskerville',serif;font-style:italic;color:var(--crimson);font-size:26px;line-height:1.4}
  .cover-year{position:absolute;right:22px;bottom:24px;color:#fff;font-weight:600;font-size:13px}

  /* paradise */
  .paradise h2{position:absolute;left:22px;top:24px;font-family:'Libre Baskerville',serif;font-size:25px;line-height:1.35;font-weight:700;letter-spacing:.5px}
  .paradise h3{position:absolute;left:22px;top:100px;font-family:'Libre Baskerville',serif;font-weight:400;color:var(--crimson);font-size:20px;line-height:1.4}
  .paradise .small{position:absolute;left:22px;top:178px;width:196px}

  /* details */
  .details h2{position:absolute;top:20px;width:100%;text-align:center;font-family:'Libre Baskerville',serif;font-size:26px;letter-spacing:1px}
  .label{font-family:'Libre Baskerville',serif;color:var(--crimson);font-weight:700;font-size:12.5px;text-transform:uppercase}
  .col{position:absolute;top:262px;width:180px}
  .col .label{margin-bottom:6px}
  .divider{position:absolute;left:216px;top:262px;width:2px;height:112px;background:var(--crimson)}
  .route{position:absolute;left:18px;top:416px}
  .route h4{font-family:'Libre Baskerville',serif;font-size:12px;font-weight:700}
  .route span{display:block;color:var(--crimson);font-size:8px;margin-top:6px;line-height:1.3}
  .map{left:14px;top:488px;width:406px;height:114px;border:2px solid var(--crimson);background:
    radial-gradient(ellipse 35% 60% at 20% 40%,rgba(250,250,250,.95),rgba(250,250,250,0) 70%),
    radial-gradient(ellipse 40% 70% at 85% 60%,rgba(196,160,120,.9),rgba(196,160,120,0) 70%),
    linear-gradient(110deg,#eeece8 0%,#d9d4cb 45%,#cdb79c 70%,#c6a987 100%)}

  /* pricing */
  .band{position:absolute;left:0;top:0;width:100%;height:57px;display:flex;align-items:center;z-index:2}
  .band.dark{background:var(--charcoal);padding-left:28px}
  .band h2{font-family:'Libre Baskerville',serif;color:#fff;font-size:25px;font-weight:700;letter-spacing:.5px}
  .pricing .label{position:absolute;left:31px;font-size:11.5px}
  .line{position:absolute;font-size:9.4px;line-height:1.45}
  .sub{position:absolute;left:48px;color:var(--crimson);font-size:9.6px;font-weight:600;text-decoration:underline}
  .blob{position:absolute;border-radius:50%;background:var(--blush)}

  /* adventures */
  .band.rose{background:var(--rose);justify-content:center}
  .caption{position:absolute;font-size:12.5px;line-height:1.3;z-index:1}
  .caption em{font-style:normal;color:var(--crimson)}

  /* lodge */
  .overlay{position:absolute;color:#fff;font-size:10px;line-height:1.3;z-index:1;text-shadow:0 1px 2px rgba(0,0,0,.5)}

  /* back */
  .contact{position:absolute;left:0;width:100%;text-align:center;font-size:8.5px;line-height:1.4}
  .contact.red{color:var(--crimson)}
</style>
</head>
<body>

<!-- Cover -->
<section class="page cover" style="top:212px">
  <div class="photo cover-photo" role="img" aria-label="Hunter kneeling beside an ibex trophy on a rocky Tian Shan slope under a cloudy sky"></div>
  <div class="brand" style="left:16px;top:30px;font-size:10px;color:#1f1f1f"><span class="dot"></span>Trailwardens</div>
  <div class="brand" style="right:16px;top:46px;font-size:10px;color:var(--crimson)">Ridgeline Outfitters</div>
  <div class="cover-title"><p>The Vorelka Crest</p><p>Lodge</p></div>
  <svg style="position:absolute;left:0;bottom:0" width="434" height="60" viewBox="0 0 434 60" aria-hidden="true">
    <path d="M170 60 C230 48 300 25 434 0 L434 60 Z" fill="var(--crimson)" opacity=".85"/>
  </svg>
  <div class="cover-year">Kyrgyzstan 2025</div>
</section>

<!-- A Hunter's Paradise -->
<section class="page paradise" style="top:872px">
  <h2>A HUNTER'S<br>PARADISE:</h2>
  <h3>Where Luxury<br>Roams Free</h3>
  <p class="small">Renowned as one of the finest mountain hunting lodges in the world, this Kyrgyzstan camp offers adventure and luxury in the majestic Tian Shan Mountains. Hunt Marco Polo sheep and Ibex across rugged terrain, then relax in unparalleled comfort. Unwind in this secluded oasis, surrounded by breathtaking panoramas of the Kyrgyz landscape. This is where the adventure of the hunt seamlessly blends with the comforts of an unparalleled wilderness retreat.</p>
  <div class="photo" style="left:232px;top:0;width:202px;height:353px;background:
    radial-gradient(ellipse 45% 30% at 50% 42%,rgba(92,96,98,.85),rgba(92,96,98,0) 70%),
    radial-gradient(ellipse 60% 25% at 45% 70%,rgba(238,236,232,.95),rgba(238,236,232,0) 70%),
    radial-gradient(ellipse 40% 15% at 75% 92%,rgba(150,60,70,.55),rgba(150,60,70,0) 70%),
    linear-gradient(180deg,#a9bbcf 0%,#96a3b0 30%,#d6d8da 60%,#efefef 85%,#cfc6c4 100%)" role="img" aria-label="Hunter seated on snow with a Marco Polo ram trophy"></div>
  <div class="photo" style="left:0;top:353px;width:434px;height:261px;background:
    radial-gradient(ellipse 30% 35% at 40% 55%,rgba(60,55,50,.9),rgba(60,55,50,0) 70%),
    radial-gradient(ellipse 35% 25% at 30% 78%,rgba(210,200,185,.8),rgba(210,200,185,0) 70%),
    linear-gradient(180deg,#4f6f93 0%,#8fa6c0 14%,#d59b8c 26%,#a7a6b0 36%,#5d6470 55%,#3b3f48 75%,#2a2c33 100%)" role="img" aria-label="Hunter with large curled-horn ram against snowy peaks at dusk"></div>
</section>

<!-- Hunt Details -->
<section class="page details" style="top:1530px">
  <div class="photo" style="left:0;top:0;width:434px;height:241px;background:
    radial-gradient(ellipse 45% 12% at 55% 60%,rgba(95,98,100,.9),rgba(95,98,100,0) 70%),
    radial-gradient(ellipse 60% 8% at 50% 73%,rgba(120,130,135,.7),rgba(120,130,135,0) 70%),
    linear-gradient(180deg,#cfd2d7 0%,#b8bcc2 40%,#85837d 58%,#8c6a4b 74%,#75523a 88%,#5f412c 100%)" role="img" aria-label="Wide valley with a lake and jagged mountains under overcast sky"></div>
  <h2>HUNT DETAILS</h2>
  <div class="col" style="left:18px">
    <div class="label">Highlights</div>
    <p class="small">Experience an unforgettable hunting adventure in Kyrgyzstan's majestic Tian Shan Mountains. Pursue the elusive Marco Polo sheep and Siberian Ibex on horseback alongside seasoned local guides. Sharpen your long-range shooting skills, as accuracy at 400-600 meters may be required. Towering peaks and vast valleys provide a stunning backdrop for truly once-in-a-lifetime experiences.</p>
  </div>
  <div class="divider"></div>
  <div class="col" style="left:232px">
    <div class="label">Property Facts</div>
    <p class="small">Nestled deep within the majestic Tian Shan mountains, this hunting camp offers an unparalleled wilderness experience. Eight luxurious rooms each provide private bathrooms and unexpected amenities like reliable WiFi. The lounge area, with striking floor-to-ceiling windows, frames breathtaking panoramic views of the rugged landscape, blending modern comfort and unspoiled wilderness.</p>
  </div>
  <div class="route"><h4>GETTING THERE</h4><span>Recommended<br>Route</span></div>
  <p class="small" style="position:absolute;left:130px;top:412px;width:290px">International flights typically arrive at Manas International Airport (FRU) in Bishkek, Kyrgyzstan, often with layovers in Istanbul or Dubai. Upon arrival our team will assist with firearms clearance. For guests arriving late, overnight accommodations in Bishkek can be arranged. From Bishkek, hunters have two options to reach the hunting area: a 12-hour scenic drive or a 2.5-hour helicopter flight.</p>
  <div class="photo map" role="img" aria-label="Map of the route from Bishkek to the hunting area"></div>
  <svg style="position:absolute;left:234px;top:518px" width="16" height="22" viewBox="0 0 16 22" aria-hidden="true">
    <path d="M8 0C3.6 0 0 3.6 0 8c0 6 8 14 8 14s8-8 8-14c0-4.4-3.6-8-8-8z" fill="#d92b2b"/><circle cx="8" cy="8" r="3" fill="#fff"/>
  </svg>
</section>

<!-- Dates & Pricing -->
<section class="page pricing" style="top:2192px">
  <div class="band dark"><h2>DATES &amp; PRICING</h2></div>
  <div class="label" style="top:76px">Season Dates</div>
  <div class="line" style="left:31px;top:100px">August 15th 2025 – November 30th 2025</div>
  <div class="label" style="top:146px">Inclusions</div>
  <div class="sub" style="top:177px">GUIDED HUNT</div>
  <div class="line" style="left:66px;top:200px">7-day guided horseback hunt for Marco Polo Argali, Ibex or Both<br>Exclusive access to some of the finest hunting areas in Kyrgyzstan<br>Trophy Skinning and field preparation</div>
  <div class="sub" style="top:254px">FOOD &amp; DRINK</div>
  <div class="line" style="left:66px;top:280px">Chef-prepared breakfast, packed lunch and dinner<br>A selection of non-alcoholic beverages</div>
  <div class="sub" style="top:316px">TRAVEL &amp; LOGISTICS</div>
  <div class="line" style="left:66px;top:339px">Pre-arrival custom planning with the Trailwardens Team<br>Round trip, fixed-time airport transfers to Bishkek</div>
  <div class="label" style="top:405px">Pricing</div>
  <div class="line" style="left:31px;top:432px;font-weight:500;line-height:2">MARCO POLO AND IBEX COMBO - $39,500 (min. 2 hunters)<br>MARCO POLO ARGALI - $32,500 (min. 2 hunters)<br>MID-ASIAN IBEX - $10,500 (Min. 2 hunters)</div>
  <div class="blob" style="left:-70px;top:520px;width:170px;height:170px"></div>
  <div class="label" style="right:28px;top:522px;left:auto">Popular Add Ons</div>
  <div class="line" style="right:30px;top:550px;text-align:right;line-height:1.8">WOLF (Opportunistic): $2,500<br>Extra Ibex $5,500</div>
</section>

<!-- The Adventures -->
<section class="page adventures" style="top:2852px">
  <div class="band rose"><h2>THE ADVENTURES</h2></div>
  <div class="photo" style="left:0;top:57px;width:252px;height:318px;background:
    radial-gradient(ellipse 55% 30% at 45% 62%,rgba(72,64,56,.9),rgba(72,64,56,0) 70%),
    radial-gradient(ellipse 30% 18% at 75% 55%,rgba(120,96,76,.8),rgba(120,96,76,0) 70%),
    radial-gradient(ellipse 60% 20% at 50% 92%,rgba(150,135,118,.9),rgba(150,135,118,0) 70%),
    linear-gradient(180deg,#ecebea 0%,#dcdbd9 26%,#b3aa9e 42%,#8a7d6f 62%,#6d5f51 82%,#5a4c3f 100%)" role="img" aria-label="Hunters on horseback posing on a rocky mountainside"></div>
  <p class="caption" style="left:16px;top:66px">A Horseback Ride<br>You'll Never Forget.<br><em>Challenging Hunts<br>For Prized Game.</em></p>
  <div class="photo" style="left:254px;top:57px;width:180px;height:164px;background:
    radial-gradient(ellipse 45% 30% at 42% 50%,rgba(80,72,62,.9),rgba(80,72,62,0) 70%),
    radial-gradient(ellipse 30% 18% at 28% 30%,rgba(176,108,60,.65),rgba(176,108,60,0) 70%),
    linear-gradient(160deg,#c4c2be 0%,#9e978d 35%,#7b7268 60%,#5a5148 100%)" role="img" aria-label="Hunter lying prone aiming a rifle on a ridge"></div>
  <div class="photo" style="left:254px;top:223px;width:180px;height:391px;background:
    radial-gradient(ellipse 60% 14% at 50% 47%,rgba(205,210,218,.9),rgba(205,210,218,0) 70%),
    radial-gradient(ellipse 35% 18% at 68% 78%,rgba(60,56,52,.85),rgba(60,56,52,0) 70%),
    radial-gradient(ellipse 60% 20% at 30% 70%,rgba(150,120,92,.8),rgba(150,120,92,0) 70%),
    linear-gradient(180deg,#f6f6f7 0%,#eceef1 30%,#c3c7cd 46%,#8e7c68 62%,#6e5c4a 82%,#4d3f33 100%)" role="img" aria-label="Hunter sitting on a snowy slope overlooking mountains"></div>
  <p class="caption" style="left:262px;top:268px;font-size:10px;text-align:right;width:164px">A Stunning Camp<br>To Revitalize Your Spirit.<br>This Is The Hunt Of A Lifetime.</p>
  <div class="photo" style="left:0;top:377px;width:252px;height:237px;background:
    radial-gradient(ellipse 30% 40% at 50% 58%,rgba(190,184,176,.9),rgba(190,184,176,0) 70%),
    radial-gradient(ellipse 25% 30% at 36% 40%,rgba(70,68,62,.85),rgba(70,68,62,0) 70%),
    radial-gradient(ellipse 70% 20% at 50% 92%,rgba(170,130,80,.85),rgba(170,130,80,0) 70%),
    linear-gradient(180deg,#c2cad5 0%,#a8a6a2 25%,#8c7f70 50%,#6e5a46 75%,#5b4733 100%)" role="img" aria-label="Hunter standing with a saddled horse in a mountain valley"></div>
</section>

<!-- The Lodge -->
<section class="page lodge" style="top:3512px">
  <div class="photo" style="left:0;top:0;width:434px;height:184px;background:
    radial-gradient(ellipse 55% 16% at 50% 66%,rgba(236,170,90,.95),rgba(236,170,90,0) 70%),
    radial-gradient(ellipse 60% 18% at 60% 40%,rgba(140,100,80,.8),rgba(140,100,80,0) 70%),
    linear-gradient(180deg,#1c3a68 0%,#325b8e 22%,#7f7f86 38%,#8a6a52 52%,#6a4830 68%,#b67a3c 78%,#4a3020 100%)" role="img" aria-label="Timber lodge lit at dusk beneath a rocky mountain"></div>
  <h2 class="serif" style="position:absolute;right:20px;top:14px;color:#fff;font-size:25px;font-weight:700;z-index:1">THE LODGE</h2>
  <div class="photo" style="left:0;top:186px;width:225px;height:190px;background:
    radial-gradient(ellipse 55% 22% at 45% 80%,rgba(40,120,100,.95),rgba(40,120,100,0) 70%),
    radial-gradient(ellipse 40% 30% at 70% 35%,rgba(220,160,90,.85),rgba(220,160,90,0) 70%),
    linear-gradient(180deg,#6b3f1e 0%,#9a6030 35%,#b0753a 55%,#5a3a22 80%,#3a2616 100%)" role="img" aria-label="Wood-panelled games room with a pool table"></div>
  <p class="overlay" style="left:16px;top:196px;width:200px">Beyond The Reach Of Ordinary Travel Lies A Hidden World Of Spectacular Beauty And Unrivaled Hunting.</p>
  <div class="photo" style="left:227px;top:186px;width:207px;height:190px;background:
    radial-gradient(ellipse 35% 25% at 50% 30%,rgba(240,200,130,.9),rgba(240,200,130,0) 70%),
    radial-gradient(ellipse 50% 20% at 55% 82%,rgba(230,220,205,.85),rgba(230,220,205,0) 70%),
    linear-gradient(160deg,#c08444 0%,#96602f 45%,#7a4c26 75%,#5a3a20 100%)" role="img" aria-label="Warm wooden lounge with armchairs"></div>
  <div class="photo" style="left:0;top:378px;width:202px;height:236px;background:
    radial-gradient(ellipse 35% 25% at 50% 52%,rgba(255,210,130,.95),rgba(255,210,130,0) 70%),
    radial-gradient(ellipse 60% 30% at 50% 20%,rgba(120,80,45,.8),rgba(120,80,45,0) 70%),
    linear-gradient(180deg,#2a1c12 0%,#5e3b1e 30%,#c98c45 52%,#6a4322 72%,#2e1f13 100%)" role="img" aria-label="Lodge exterior with glowing timber gable at night"></div>
  <div class="photo" style="left:204px;top:378px;width:230px;height:236px;background:
    radial-gradient(ellipse 50% 20% at 55% 78%,rgba(225,210,190,.95),rgba(225,210,190,0) 70%),
    radial-gradient(ellipse 25% 18% at 30% 50%,rgba(90,60,40,.8),rgba(90,60,40,0) 70%),
    linear-gradient(180deg,#8e5f35 0%,#b0814f 40%,#c9a679 62%,#9a7552 82%,#6e4e33 100%)" role="img" aria-label="Lounge with sofas and mounted trophies on timber walls"></div>
  <p class="overlay" style="right:14px;top:388px;width:200px;text-align:right;font-size:9.5px">Our Kyrgyzstan Experience Is Crafted For The Discerning Sportsman, Offering Access To Pristine Wilderness And Luxurious Accommodations. This Is Hunting Elevated To An Art Form.</p>
</section>

<!-- Back cover -->
<section class="page back" style="top:4172px">
  <div class="brand" style="left:0;width:100%;justify-content:center;top:250px;font-size:14px;color:#1f1f1f"><span class="dot"></span>Trailwardens</div>
  <div class="brand" style="left:0;width:100%;justify-content:center;top:398px;font-size:15px;color:var(--crimson)">Ridgeline Outfitters</div>
  <div class="blob" style="right:-60px;top:520px;width:150px;height:150px"></div>
  <div class="contact red" style="top:558px">+961 5550 1234<br>www.trailwardens.com</div>
  <div style="position:absolute;left:138px;top:584px;width:158px;height:1px;background:var(--ink)"></div>
  <div class="contact" style="top:589px">lena.marsh@trailwardens.com</div>
</section>

</body>
</html>
```